Business card for event manager / organizer "waiter service"

Draft of a new valuable business card for my company.
Events, personnel service providers, festivals

```html
<!DOCTYPE html>
<html lang="de">
<head>
<meta charset="utf-8">
<title>Jonas Servicecrew – Visitenkarte</title>
<link href="https://fonts.googleapis.com/css2?family=Montserrat:wght@400;500;700&display=swap" rel="stylesheet">
<style>
  :root {
    --backdrop: #d2d2d2;
    --card-dark: #141212;
    --card-glow: #3a2f1c;
    --gold: #c9a24a;
    --white: #ffffff;
    --ink: #1a1a1a;
    --orange: #e8731a;
    --muted: #8a8a8a;
    --photo-top: #2a2620;
    --photo-bottom: #0c0b0b;
  }
  * { box-sizing: border-box; margin: 0; padding: 0; }
  html, body { width: 1200px; height: 1200px; overflow: hidden; }
  body {
    background: var(--backdrop);
    font-family: "Montserrat", sans-serif;
    position: relative;
  }
  .card {
    position: absolute;
    left: 150px;
    width: 900px;
    height: 530px;
    box-shadow: 0 10px 30px rgba(0,0,0,.22);
    overflow: hidden;
  }
  .card--front {
    top: 45px;
    background:
      radial-gradient(ellipse 70% 40% at 55% 28%, var(--card-glow), transparent 70%),
      linear-gradient(180deg, #2a241a 0%, var(--card-dark) 55%, #0e0d0d 100%);
    color: var(--gold);
  }
  .card--back {
    top: 625px;
    background: var(--white);
  }
  .portrait {
    position: absolute;
    left: 175px;
    top: 70px;
    width: 200px;
    height: 255px;
    border-radius: 60px 60px 6px 6px;
    background: linear-gradient(180deg, var(--photo-top), var(--photo-bottom));
  }
  .holder {
    position: absolute;
    left: 540px;
    top: 190px;
    white-space: nowrap;
  }
  .holder__name { font-size: 36px; font-weight: 700; letter-spacing: .5px; line-height: 1.1; }
  .holder__role { font-size: 22px; font-weight: 400; margin-top: 2px; }
  .contact-list {
    position: absolute;
    bottom: 98px;
    list-style: none;
    font-size: 21px;
    font-weight: 500;
    white-space: nowrap;
  }
  .contact-list li { display: flex; align-items: center; gap: 14px; height: 34px; }
  .contact-list svg { width: 19px; height: 19px; flex: none; }
  .contact-list--left { left: 95px; }
  .contact-list--right { left: 510px; }
  .divider {
    position: absolute;
    left: 95px;
    right: 60px;
    top: 440px;
    height: 2px;
    background: var(--gold);
  }
  .brand {
    position: absolute;
    left: 0; right: 0;
    top: 205px;
    display: flex;
    flex-direction: column;
    align-items: center;
  }
  .brand__row { display: flex; align-items: center; gap: 22px; }
  .brand__mark { width: 70px; height: 70px; background: var(--orange); }
  .brand__name { font-size: 54px; font-weight: 700; color: var(--ink); letter-spacing: 1px; white-space: nowrap; }
  .brand__tagline { margin-top: 14px; font-size: 20px; color: var(--muted); font-weight: 400; }
</style>
</head>
<body>

<section class="card card--front">
  <div class="portrait" role="img" aria-label="Portraitfoto des Inhabers in dunklem Hemd"></div>

  <div class="holder">
    <div class="holder__name">Jonas Beckmann</div>
    <div class="holder__role">Inhaber</div>
  </div>

  <ul class="contact-list contact-list--left">
    <li>
      <svg viewBox="0 0 24 24" fill="currentColor"><path d="M6.6 10.8a15 15 0 0 0 6.6 6.6l2.2-2.2a1 1 0 0 1 1-.25 11.4 11.4 0 0 0 3.6.57 1 1 0 0 1 1 1V20a1 1 0 0 1-1 1A17 17 0 0 1 3 4a1 1 0 0 1 1-1h3.5a1 1 0 0 1 1 1c0 1.250.2 2.450.57 3.570a1 1 0 0 1-.25 1z"/></svg>
      02361 555 20 40
    </li>
    <li>
      <svg viewBox="0 0 24 24" fill="currentColor"><path d="M6.6 10.8a15 15 0 0 0 6.6 6.6l2.2-2.2a1 1 0 0 1 1-.25 11.4 11.4 0 0 0 3.6.57 1 1 0 0 1 1 1V20a1 1 0 0 1-1 1A17 17 0 0 1 3 4a1 1 0 0 1 1-1h3.5a1 1 0 0 1 1 1c0 1.250.2 2.450.57 3.570a1 1 0 0 1-.25 1z"/></svg>
      0170 555 31 72
    </li>
    <li>
      <svg viewBox="0 0 24 24" fill="currentColor"><circle cx="12" cy="12" r="10"/></svg>
      jonasservicecrew
    </li>
  </ul>

  <div class="divider"></div>

  <ul class="contact-list contact-list--right">
    <li>
      <svg viewBox="0 0 24 24" fill="currentColor"><path d="M2 5h20v14H2z"/><path d="M2 5l10 8 10-8" fill="none" stroke="#141212" stroke-width="2"/></svg>
      info@jonas-servicecrew.de
    </li>
    <li>
      <svg viewBox="0 0 24 24" fill="none" stroke="currentColor" stroke-width="2"><circle cx="12" cy="12" r="9.5"/><path d="M2.5 12h19M12 2.5c3 3.3 3 15.7 0 19M12 2.5c-3 3.3-3 15.7 0 19"/></svg>
      www.jonas-servicecrew.de
    </li>
    <li>
      <svg viewBox="0 0 24 24" fill="currentColor"><path d="M12 2a7 7 0 0 0-7 7c0 5 7 13 7 13s7-8 7-13a7 7 0 0 0-7-7zm0 9.5A2.5 2.5 0 1 1 12 6.5a2.5 2.5 0 0 1 0 5z"/></svg>
      Lindenweg 12, 45701 Herten
    </li>
  </ul>
</section>

<section class="card card--back">
  <div class="brand">
    <div class="brand__row">
      <div class="brand__mark"></div>
      <div class="brand__name">JONAS SERVICECREW</div>
    </div>
    <div class="brand__tagline">Personal für Events, Feste und Festivals</div>
  </div>
</section>

</body>
</html>
```